Kistenhalle
Zielgruppe
Kistenhalle.de vermietet Lagercontainern an Privatkunden und Gewerbetriebende
Vermietung von Stellfächen für Wohnmobile/Boote etc
Das ganze auf einem Gewerbegelände in Köln (Brauweiler)
Aufgabenstellung
Erstellung eines 2-Seitigen DIN lang (10,5 x 21 cm) Flyers
Seite A: Vermietung von Lagercontainern
Seite B: Stellfächen für Wohnmobile/Boote
Wichtig: Die Sicherheit (Zutrittskontrolle, Videoüberwachung, Brandmeldeanlage)
Preise sollen auf Flyern erscheinen, diese wie auch die Textee möchte ich jedoch ändern können.
Alle Texte können auch von der Seite kistenhalle.de übernommen werden
Das Logo (siehe hallen_quartier.ai) müsste noch bearbeitet werden .... also "hallenquartier" raus und dafür "Lagerraum Container" rein
Gerne mit Symbolen arbeiten ..

```html
<!DOCTYPE html>
<html lang="de">
<head>
<meta charset="utf-8">
<title>Kistenhalle – Lagercontainer Flyer</title>
<link href="https://fonts.googleapis.com/css2?family=Roboto+Condensed:wght@500;700&family=Source+Sans+3:wght@400;600;700&display=swap" rel="stylesheet">
<style>
  :root{
    --navy:#13294b;
    --red:#a6122b;
    --orange:#ec7404;
    --white:#ffffff;
    --text:#1b2a47;
    --grey:#7a7f88;
  }
  *{margin:0;padding:0;box-sizing:border-box}
  html,body{width:1200px;height:2400px;overflow:hidden;background:var(--white)}
  .flyer{position:relative;width:1200px;height:2400px;font-family:"Source Sans 3",sans-serif;color:var(--text)}
  .header{position:absolute;left:0;top:0;width:1200px;height:339px;background:var(--navy)}
  .brand{position:absolute;left:102px;top:58px;width:995px;height:232px;border:7px solid var(--white);border-radius:26px;display:flex;align-items:center;justify-content:center;gap:48px}
  .brand-square{width:120px;height:120px;background:var(--white);border-radius:8px}
  .brand-name{font-family:"Roboto Condensed",sans-serif;font-weight:700;font-size:124px;color:var(--white);letter-spacing:2px;text-transform:uppercase}
  .claims{position:absolute;left:0;top:354px;width:1200px;height:136px;background:var(--red);display:flex;align-items:center;justify-content:center;gap:58px}
  .claim{display:flex;align-items:center;gap:16px;color:var(--white);font-weight:700;font-size:68px}
  .claim svg{width:52px;height:52px}
  .benefits{position:absolute;left:46px;top:538px;width:1109px;height:958px;border:7px solid var(--navy);border-radius:18px}
  .benefit-label{position:absolute;left:40px;font-weight:600;font-size:52px;line-height:60px;color:var(--navy)}
  .benefit-text{position:absolute;left:347px;width:740px;font-size:38px;line-height:58.5px;white-space:nowrap}
  .benefit-icon{position:absolute}
  .location{position:absolute;left:0;top:1542px;width:1200px;height:205px;background:var(--orange);color:var(--white)}
  .location svg{position:absolute;left:52px;top:42px;width:74px;height:116px}
  .location p{position:absolute;left:168px;top:32px;font-weight:700;font-size:50px;line-height:70px;white-space:nowrap}
  .parking-title{position:absolute;left:0;top:1800px;width:1200px;text-align:center;font-family:"Roboto Condensed",sans-serif;font-weight:500;font-size:52px;color:var(--navy)}
  .camper-photo{position:absolute;left:39px;top:1887px;width:541px;height:330px;background:linear-gradient(180deg,#ffffff 0%,#eef0f3 55%,#d9dde2 100%);border-radius:6px}
  .price-box{position:absolute;left:623px;top:1898px;width:528px;height:304px;background:var(--navy);border-radius:12px;color:var(--white)}
  .price-box::after{content:"";position:absolute;inset:10px;border:3px solid var(--white);border-radius:8px;pointer-events:none}
  .price{position:absolute;left:48px;top:32px;font-weight:700;font-size:66px}
  .price small{font-size:32px;font-weight:600;margin-left:8px}
  .features{position:absolute;left:48px;top:134px;list-style:none}
  .features li{display:flex;align-items:center;gap:12px;font-weight:700;font-size:29.5px;line-height:46px}
  .features svg{width:26px;height:26px}
  .footnote{position:absolute;left:0;top:2232px;width:1200px;text-align:center;font-size:19px;color:var(--grey)}
  .contact{position:absolute;left:0;top:2283px;width:1200px;height:117px;background:var(--navy);display:flex;align-items:center;justify-content:center;gap:60px;color:var(--white);font-weight:600;font-size:35px}
  .contact span{display:flex;align-items:center;gap:12px}
  .contact svg{width:32px;height:32px}
</style>
</head>
<body>
<div class="flyer">
  <header class="header">
    <div class="brand">
      <div class="brand-square"></div>
      <div class="brand-name">Kistenhalle</div>
    </div>
  </header>

  <section class="claims">
    <div class="claim"><svg viewBox="0 0 24 24"><circle cx="12" cy="12" r="12" fill="#fff"/><path d="M6.5 12.5l3.6 3.5 7.4-7.6" fill="none" stroke="#a6122b" stroke-width="3" stroke-linecap="round" stroke-linejoin="round"/></svg>Günstig</div>
    <div class="claim"><svg viewBox="0 0 24 24"><circle cx="12" cy="12" r="12" fill="#fff"/><path d="M6.5 12.5l3.6 3.5 7.4-7.6" fill="none" stroke="#a6122b" stroke-width="3" stroke-linecap="round" stroke-linejoin="round"/></svg>Sicher</div>
    <div class="claim"><svg viewBox="0 0 24 24"><circle cx="12" cy="12" r="12" fill="#fff"/><path d="M6.5 12.5l3.6 3.5 7.4-7.6" fill="none" stroke="#a6122b" stroke-width="3" stroke-linecap="round" stroke-linejoin="round"/></svg>Lagern</div>
  </section>

  <section class="benefits">
    <h2 class="benefit-label" style="top:36px">Mehr Platz</h2>
    <svg class="benefit-icon" style="left:96px;top:142px;width:139px;height:135px" viewBox="0 0 139 135">
      <rect x="38" y="0" width="62" height="62" rx="9" fill="#13294b"/>
      <rect x="0" y="72" width="62" height="62" rx="9" fill="#13294b"/>
      <rect x="77" y="72" width="62" height="62" rx="9" fill="#13294b"/>
    </svg>
    <p class="benefit-text" style="top:38px">Verschaffen Sie sich mehr Platz! Ob privat<br>(Umzug, fehlende Garage, voller Keller)<br>oder gewerblich (zur Lagerung von Akten,<br>Gerätepark, Warenlager) – nutzen Sie Lager-<br>container zur Platzoptimierung.</p>

    <h2 class="benefit-label" style="top:361px">Ebenerdig</h2>
    <svg class="benefit-icon" style="left:96px;top:467px;width:150px;height:100px" viewBox="0 0 150 100">
      <rect x="43" y="0" width="64" height="64" rx="9" fill="#13294b"/>
      <rect x="0" y="86" width="150" height="8" fill="#13294b"/>
    </svg>
    <p class="benefit-text" style="top:363px">Auf dem befestigten Gelände können Sie auch<br>mit großen Fahrzeugen direkt an die Lager-<br>container heranfahren und bequem be- oder<br>entladen, ohne große Wege gehen zu müssen.</p>

    <h2 class="benefit-label" style="top:627px">Rentabel</h2>
    <svg class="benefit-icon" style="left:107px;top:734px;width:118px;height:118px" viewBox="0 0 118 118">
      <circle cx="59" cy="59" r="59" fill="#13294b"/>
      <circle cx="59" cy="59" r="48" fill="none" stroke="#fff" stroke-width="4"/>
      <text x="59" y="78" text-anchor="middle" font-family="Source Sans 3, sans-serif" font-weight="700" font-size="56" fill="#fff">€</text>
    </svg>
    <p class="benefit-text" style="top:630px">Nutzen Sie den Platz in Ihrer Wohnung oder<br>Firma rentabler und lagern Sie die wichtigen,<br>aber nicht täglich benötigten Dinge in einen<br>großen Lagerraum aus. Und das zu fairen<br>Preisen bei Top-Konditionen.</p>
  </section>

  <section class="location">
    <svg viewBox="0 0 74 116"><path d="M37 3C18 3 4 17 4 36c0 22 33 77 33 77s33-55 33-77C70 17 56 3 37 3z" fill="#fff"/><circle cx="37" cy="35" r="13" fill="#ec7404"/></svg>
    <p>Sie finden uns in der Lindenhofstraße 72<br>im Gewerbegebiet Hohenfeld-Westwinkel</p>
  </section>

  <h2 class="parking-title">AUCH STELLFLÄCHEN FÜR WOHNMOBILE / BOOTE</h2>
  <div class="camper-photo" role="img" aria-label="Foto eines weißen Wohnmobils in Seitenansicht"></div>

  <div class="price-box">
    <div class="price">40,- €<small>pro Monat *</small></div>
    <ul class="features">
      <li><svg viewBox="0 0 24 24"><circle cx="12" cy="12" r="12" fill="#fff"/><path d="M6.5 12.5l3.6 3.5 7.4-7.6" fill="none" stroke="#13294b" stroke-width="3" stroke-linecap="round" stroke-linejoin="round"/></svg>Durchgehend zugänglich</li>
      <li><svg viewBox="0 0 24 24"><circle cx="12" cy="12" r="12" fill="#fff"/><path d="M6.5 12.5l3.6 3.5 7.4-7.6" fill="none" stroke="#13294b" stroke-width="3" stroke-linecap="round" stroke-linejoin="round"/></svg>14m² Lagerkapazität</li>
      <li><svg viewBox="0 0 24 24"><circle cx="12" cy="12" r="12" fill="#fff"/><path d="M6.5 12.5l3.6 3.5 7.4-7.6" fill="none" stroke="#13294b" stroke-width="3" stroke-linecap="round" stroke-linejoin="round"/></svg>Versicherungsschutz möglich</li>
    </ul>
  </div>

  <p class="footnote">*Preis gilt pro Monat und Container für private Vermietung, bei gewerblicher Anmietung zzgl. 19% MwSt</p>

  <footer class="contact">
    <span><svg viewBox="0 0 24 24"><circle cx="12" cy="7" r="5" fill="#fff"/><path d="M3 23c0-6 4-9 9-9s9 3 9 9z" fill="#fff"/></svg>04721 5550187</span>
    <span><svg viewBox="0 0 24 24"><rect x="1" y="4" width="22" height="16" rx="2" fill="#fff"/><path d="M2 5l10 8 10-8" fill="none" stroke="#13294b" stroke-width="2"/></svg>info@kistenhalle.de</span>
    <span><svg viewBox="0 0 24 24"><circle cx="12" cy="12" r="11" fill="#fff"/><g fill="none" stroke="#13294b" stroke-width="1.6"><ellipse cx="12" cy="12" rx="5" ry="11"/><path d="M1 12h22M3 6.5h18M3 17.5h18"/></g></svg>kistenhalle.de</span>
  </footer>
</div>
</body>
</html>
```